Business card for Crestline Bathrooms

Please design a business card for our bathroom renovation business. You can use my existing logo, but if you have an idea to modernize it, I would like to see it. Please see attached files first. I would like to use the blue and the orange theme. I like the concept of using the shower head in the logo. Please find following a design (or two) that I have been trying to create with my limited resources. That design was for a sign, but I was going to adopt it and use it as a business card as well. I like the concept of the water splash but I don’t think it “flows” nicely together with the logo. Another thought is that maybe creating the logo out of water splash could work and have a dramatic effect (like the water text and the butterfly picture attached with similar background instead of white). If the above doesn’t work I would like to see a modern simplified design. One of the attached files named as the unwanted business card has all the details that I want included in the business card. Please note that it is two sided.
Updates

I am very thankful for the designs that I have received, but they are very similar and only a couple of attempts to do something with the water splash as per my original brief. Modernizing the logo and having it made out of out of water splash with the orange as color accent could work and have a dramatic effect (like the water text and the butterfly picture attached with similar background instead of white). Please do not use the butterfly itself! This is just an example that images can be created out of water splash.

Contact Information for Business Card

all the details are on the unwonted business card file included

Colors
3176b5

Requirements
Nice to have
• Copied from the brief:
• ... maybe creating the logo out of water splash could work and have a dramatic effect (like the water text and the butterfly picture attached with similar background instead of white). Please do not use the butterfly itself!
Should not have
• I am getting designs with a butterfly. The butterfly picture was an example of creating something from a water splash. The butterfly itself has no association with anything other than the concept of creating a logo out of water splash. Sorry, I thought I was clear in the brief.

```html
<!DOCTYPE html>
<html lang="en">
<head>
<meta charset="utf-8">
<title>Crestline Bathrooms – Business Card</title>
<link rel="stylesheet" href="https://fonts.googleapis.com/css2?family=Roboto:wght@400;500&family=Roboto+Condensed:wght@700&display=swap">
<style>
  :root {
    --navy: #0d3f6b;
    --coral: #e8786c;
    --paper: #f3f3f3;
    --white: #ffffff;
    --backdrop: #2b2b2b;
    --text-font: "Roboto", Arial, sans-serif;
    --name-font: "Roboto Condensed", "Arial Narrow", sans-serif;
  }
  * { box-sizing: border-box; margin: 0; padding: 0; }
  html, body { width: 1200px; height: 960px; overflow: hidden; }
  body { background: var(--backdrop); position: relative; font-family: var(--text-font); }

  .card {
    position: absolute;
    width: 600px;
    height: 342px;
    border-radius: 22px;
    overflow: hidden;
  }
  .card--front { left: 322px; top: 108px; background: var(--paper); }
  .card--back  { left: 320px; top: 493px; background: var(--coral); }

  .front-waves { position: absolute; inset: 0; }

  .contact {
    position: absolute;
    right: 32px;
    top: 24px;
    text-align: right;
    color: var(--white);
  }
  .contact__name {
    font-family: var(--name-font);
    font-weight: 700;
    font-size: 21px;
    color: var(--coral);
    letter-spacing: 0.2px;
    margin-bottom: 10px;
  }
  .contact__address { font-size: 14.5px; line-height: 18px; margin-bottom: 9px; }
  .contact__list { list-style: none; font-size: 14.5px; line-height: 19.5px; }
  .contact__list li { display: flex; justify-content: flex-end; align-items: center; gap: 9px; }
  .contact__icon { width: 12px; height: 12px; margin-right: -24px; position: relative; left: 0; }
  .contact__list li span { margin-right: 24px; }
  .contact__list li { position: relative; }
  .contact__list li svg { position: absolute; right: 0; top: 4px; width: 12px; height: 12px; }

  .brand-mark {
    position: absolute;
    left: 36px;
    top: 182px;
    display: flex;
    align-items: center;
    gap: 12px;
    color: var(--navy);
    font-weight: 500;
    font-size: 30px;
    line-height: 34px;
  }
  .brand-mark__dot { width: 34px; height: 34px; border-radius: 50%; background: var(--coral); flex: none; }

  .back-mark {
    position: absolute;
    left: 0; right: 0;
    top: 82px;
    text-align: center;
    color: var(--white);
    font-weight: 500;
    font-size: 36px;
    line-height: 40px;
  }
  .services {
    position: absolute;
    left: 0; right: 0;
    top: 187px;
    list-style: none;
    text-align: center;
    color: var(--white);
    font-size: 14.5px;
    line-height: 18px;
  }
  .memberships {
    position: absolute;
    left: 0; right: 0;
    top: 273px;
    display: flex;
    justify-content: center;
    align-items: center;
    gap: 16px;
  }
  .badge { background: var(--white); border-radius: 4px; }
  .badge--round { width: 32px; height: 34px; border-radius: 8px; }
  .badge--wide { width: 116px; height: 26px; }
  .memberships__divider { width: 1px; height: 34px; background: var(--white); }
</style>
</head>
<body>

  <section class="card card--front" aria-label="Business card front">
    <svg class="front-waves" viewBox="0 0 600 342" preserveAspectRatio="none" aria-hidden="true">
      <path d="M0,0 H600 V228 C585,262 520,290 420,238 C300,170 150,60 0,98 Z" fill="var(--coral)"/>
      <path d="M0,0 H600 V188 C580,222 520,244 420,198 C300,140 150,58 0,88 Z" fill="var(--navy)"/>
      <path d="M0,91 C150,62 300,143 420,201 C520,247 580,225 600,190" fill="none" stroke="var(--white)" stroke-width="2"/>
    </svg>

    <div class="contact">
      <h1 class="contact__name">DANIEL HARTWELL</h1>
      <p class="contact__address">PO Box 41<br>Marlowe Creek 2804</p>
      <ul class="contact__list">
        <li><span>0412 555 018</span>
          <svg viewBox="0 0 12 12"><path d="M2.4 0.8 L4.4 0.8 L5.2 3.4 L3.9 4.4 C4.6 6 5.9 7.3 7.6 8.1 L8.6 6.8 L11.2 7.6 L11.2 9.6 C11.2 10.6 10.4 11.2 9.4 11.1 C4.8 10.6 1.4 7.2 0.9 2.6 C0.8 1.6 1.4 0.8 2.4 0.8 Z" fill="var(--coral)"/></svg>
        </li>
        <li><span>6255 0147</span>
          <svg viewBox="0 0 12 12"><rect x="2.5" y="0.5" width="7" height="11" rx="1.3" fill="none" stroke="var(--coral)" stroke-width="1.3"/><circle cx="6" cy="9.6" r="0.8" fill="var(--coral)"/></svg>
        </li>
        <li><span>daniel@crestlinebathrooms.com.au</span>
          <svg viewBox="0 0 12 12"><rect x="0.5" y="2" width="11" height="8" rx="1" fill="var(--coral)"/><path d="M0.8 2.4 L6 6.6 L11.2 2.4" fill="none" stroke="var(--navy)" stroke-width="0.9"/></svg>
        </li>
        <li><span>crestlinebathrooms.com.au</span>
          <svg viewBox="0 0 12 12"><circle cx="6" cy="6" r="5.5" fill="var(--coral)"/><path d="M0.8 6 H11.2 M6 0.6 C3.8 3 3.8 9 6 11.4 M6 0.6 C8.2 3 8.2 9 6 11.4" fill="none" stroke="var(--navy)" stroke-width="0.8"/></svg>
        </li>
      </ul>
    </div>

    <div class="brand-mark">
      <span class="brand-mark__dot"></span>
      <span class="brand-mark__name">Crestline<br>Bathrooms</span>
    </div>
  </section>

  <section class="card card--back" aria-label="Business card back">
    <p class="back-mark">Crestline Bathrooms</p>
    <ul class="services">
      <li>Complete Bathroom Renovations &amp; Remodelling</li>
      <li>Highly Skilled &amp; Qualified Tradespeople</li>
      <li>Professional Service From Concept To Completion</li>
      <li>All Work Guaranteed</li>
    </ul>
    <div class="memberships" aria-label="Industry memberships">
      <span class="badge badge--round"></span>
      <span class="memberships__divider"></span>
      <span class="badge badge--wide"></span>
    </div>
  </section>

</body>
</html>
```